Email signature and business card

Australian company called Brakmere. We provide construction and maintenance services to the mining industry. I would like the design to be similar to our website theme(www.brakmere.com.au) whilst staying compact. RGB colours to include: 42,96,140 and 232,163,0 and I have attached 2 logos.

The following fields will need to be included:

Full Name
Title
Location/Project
Phone
Mobile
Fax
Email
Web site

Target Market(s)

Mining Industry

Industry/Entity Type

Construction

Requirements
Must have
• Full Name, Title, Office Address, Phone, Mobile, Fax, Email, Web address
• Back of card must include: Boilermaking, Carpentry, Concrete, Construction, Cranes, Data and Comms, Electrical, Fabrication, Fitting, Labour Hire, Plumbing, Rigging, Shutdowns

```html
<!DOCTYPE html>
<html lang="en">
<head>
<meta charset="utf-8">
<title>Brakmere Business Card</title>
<link href="https://fonts.googleapis.com/css2?family=Open+Sans:wght@400;600;700;800&display=swap" rel="stylesheet">
<style>
  :root {
    --brand-blue: #2a608c;
    --brand-gold: #e8a300;
    --ink: #2b2b2b;
    --rule: #c9c9c9;
    --card: #ffffff;
    --backdrop: #e6e6e4;
  }
  * { box-sizing: border-box; margin: 0; padding: 0; }
  html, body { width: 1200px; height: 871px; overflow: hidden; }
  body {
    background: var(--backdrop);
    font-family: "Open Sans", Arial, sans-serif;
    color: var(--ink);
    position: relative;
  }
  .card {
    position: absolute;
    width: 560px;
    height: 320px;
    background: var(--card);
    box-shadow: 0 6px 18px rgba(0,0,0,0.18);
    overflow: hidden;
  }
  .card--back { left: 50px; top: 110px; }
  .card--front { left: 590px; top: 440px; }

  /* Back side */
  .brand-lockup {
    position: absolute;
    left: 0; right: 0; top: 36px;
    display: flex; flex-direction: column; align-items: center;
  }
  .brand-dot {
    width: 100px; height: 100px; border-radius: 50%;
    background: var(--brand-blue);
  }
  .brand-name {
    margin-top: 12px;
    font-weight: 800; font-size: 32px; letter-spacing: 0.5px;
    color: var(--brand-blue);
    text-transform: uppercase;
    line-height: 1;
  }
  .brand-web {
    margin-top: 8px;
    font-weight: 700; font-size: 14px;
    color: var(--brand-blue);
  }
  .services {
    position: absolute;
    left: 40px; right: 40px; top: 246px;
    display: flex; flex-wrap: wrap; justify-content: center;
    column-gap: 0; row-gap: 4px;
    list-style: none;
    font-size: 11px; font-weight: 600;
    color: var(--brand-blue);
  }
  .services li { padding: 0 7px; border-left: 1px solid var(--brand-gold); line-height: 1.2; }
  .services li.services__first { border-left: none; }

  /* Front side */
  .person { position: absolute; left: 50px; top: 30px; }
  .person__name { font-weight: 700; font-size: 19px; color: var(--brand-blue); letter-spacing: 0.5px; line-height: 1.3; }
  .person__title { font-size: 12px; margin-top: 2px; }
  .divider {
    position: absolute; left: 0; top: 86px; width: 380px;
    border-top: 1px solid var(--rule);
  }
  .company { position: absolute; left: 50px; top: 96px; }
  .company__name { font-weight: 700; font-size: 12px; color: var(--brand-blue); }
  .company__address { font-size: 13px; margin-top: 4px; }
  .contacts {
    position: absolute; left: 50px; top: 144px;
    display: grid; grid-template-columns: 140px 190px; row-gap: 8px;
    font-size: 13px;
  }
  .contact { display: flex; align-items: center; gap: 10px; }
  .contact svg { width: 16px; height: 16px; flex: none; }
  .front-brand {
    position: absolute; right: 36px; top: 56px;
    display: flex; flex-direction: column; align-items: center;
  }
  .front-brand .brand-dot { width: 90px; height: 90px; }
  .front-brand .brand-name { font-size: 22px; margin-top: 10px; }
  .wave { position: absolute; left: 0; top: 0; width: 560px; height: 320px; }
</style>
</head>
<body>

<section class="card card--back" aria-label="Card back">
  <div class="brand-lockup">
    <div class="brand-dot"></div>
    <div class="brand-name">Brakmere</div>
    <div class="brand-web">www.brakmere.com.au</div>
  </div>
  <ul class="services">
    <li class="services__first">Boilermaking</li>
    <li>Carpentry</li>
    <li>Concrete</li>
    <li>Construction</li>
    <li>Cranes</li>
    <li>Data and Comms</li>
    <li>Electrical</li>
    <li class="services__first">Fabrication</li>
    <li>Fitting</li>
    <li>Labour Hire</li>
    <li>Plumbing</li>
    <li>Rigging</li>
    <li>Shutdowns</li>
  </ul>
</section>

<section class="card card--front" aria-label="Card front">
  <svg class="wave" viewBox="0 0 560 320" aria-hidden="true">
    <path d="M0 222 C180 252 380 262 560 300 L560 320 L0 320 Z" fill="var(--brand-blue)"/>
    <path d="M0 210 C180 242 380 252 560 288" fill="none" stroke="var(--brand-gold)" stroke-width="3"/>
  </svg>

  <div class="person">
    <div class="person__name">Mara Leeson</div>
    <div class="person__title">CEO</div>
  </div>
  <div class="divider"></div>
  <div class="company">
    <div class="company__name">Brakmere, Inc</div>
    <div class="company__address">18 Ironbark Road, Kalden WA 6107</div>
  </div>

  <div class="contacts">
    <div class="contact">
      <svg viewBox="0 0 16 16"><path d="M3 6 Q8 1 13 6 L11 7 Q8 5 5 7 Z M4 8 H12 L13 14 H3 Z" fill="none" stroke="var(--brand-gold)" stroke-width="1.4"/></svg>
      <span>08 5550 1020</span>
    </div>
    <div class="contact">
      <svg viewBox="0 0 16 16"><rect x="4" y="1.5" width="8" height="4" fill="none" stroke="var(--brand-gold)" stroke-width="1.4"/><rect x="2" y="5.5" width="12" height="6" fill="none" stroke="var(--brand-gold)" stroke-width="1.4"/><rect x="4" y="10" width="8" height="4.5" fill="none" stroke="var(--brand-gold)" stroke-width="1.4"/></svg>
      <span>08 5550 1021</span>
    </div>
    <div class="contact">
      <svg viewBox="0 0 16 16"><rect x="4.5" y="1" width="7" height="14" rx="1.5" fill="none" stroke="var(--brand-gold)" stroke-width="1.4"/><line x1="7" y1="12.5" x2="9" y2="12.5" stroke="var(--brand-gold)" stroke-width="1.4"/></svg>
      <span>0455 501 020</span>
    </div>
    <div class="contact">
      <svg viewBox="0 0 16 16"><rect x="1.5" y="3.5" width="13" height="9" fill="none" stroke="var(--brand-gold)" stroke-width="1.4"/><path d="M1.5 3.5 L8 9 L14.5 3.5" fill="none" stroke="var(--brand-gold)" stroke-width="1.4"/></svg>
      <span>mara@brakmere.com.au</span>
    </div>
  </div>

  <div class="front-brand">
    <div class="brand-dot"></div>
    <div class="brand-name">Brakmere</div>
  </div>
</section>

</body>
</html>
```